Strategic Objective - Internal

Take text supplied in a word document and make a stylish, professional document using elements of our brand .This is an internal document for presentation to our small team . Have attached an example document - please do not copy this - this is just to give you the concept. I would like to be able to edit the text in the document you supply back to me also (In word or photoshop)

Our website is www.brolgatrade.com.au

Have attached out logo
Thank you

Target Market(s)

Our staff

Industry/Entity Type

Mining, Earthmoving

Requirements
Must have
• Professional, stylish presentation
Nice to have
• Our market includes Australia, Papua New Guinea and teh South Pacific - any graphic that supports this. We are an importer and exporter - any graphics that support this.

```html
<!DOCTYPE html>
<html lang="en">
<head>
<meta charset="utf-8">
<title>Our Core Values – Brolga Trade</title>
<link rel="stylesheet" href="https://fonts.googleapis.com/css2?family=Roboto:wght@300;400;500;700&display=swap">
<style>
  :root {
    --navy: #3a4182;
    --green: #8cc043;
    --yellow: #fbc200;
    --charcoal: #262626;
    --panel: #f0f0f0;
    --page: #ffffff;
    --ring-inner: #e2e2e2;
    --heading: #111111;
    --body: #3a3a3a;
  }
  html, body {
    margin: 0;
    padding: 0;
    overflow: hidden;
    background: var(--page);
  }
  .sheet {
    position: relative;
    width: 900px;
    height: 1200px;
    overflow: hidden;
    background: var(--page);
    font-family: "Roboto", Arial, sans-serif;
  }
  .values-panel {
    position: absolute;
    left: 0;
    top: 0;
    width: 900px;
    height: 810px;
    background: var(--panel);
  }
  .brand {
    position: absolute;
    left: 632px;
    top: 52px;
    display: flex;
    align-items: center;
    gap: 9px;
  }
  .brand-dot {
    width: 30px;
    height: 30px;
    border-radius: 50%;
    background: var(--green);
  }
  .brand-name {
    font-weight: 700;
    font-size: 22px;
    letter-spacing: 0.3px;
    color: var(--navy);
  }
  .values-diagram {
    position: absolute;
    left: 0;
    top: 0;
    width: 900px;
    height: 1200px;
  }
  .values-title {
    position: absolute;
    left: 76px;
    top: 404px;
    width: 240px;
    margin: 0;
    text-align: center;
    font-weight: 700;
    font-size: 40px;
    line-height: 51px;
    color: var(--navy);
  }
  .value {
    position: absolute;
  }
  .value-name {
    margin: 0 0 9px;
    font-weight: 500;
    font-size: 22.5px;
    line-height: 26px;
    color: var(--heading);
  }
  .value-text {
    margin: 0;
    font-weight: 300;
    font-size: 15.5px;
    line-height: 22px;
    color: var(--body);
    white-space: nowrap;
  }
  .value--excellence { left: 335px; top: 167px; width: 450px; }
  .value--accuracy   { left: 485px; top: 317px; width: 290px; }
  .value--growth     { left: 485px; top: 479px; width: 260px; }
  .value--respect    { left: 339px; top: 629px; width: 260px; }
</style>
</head>
<body>
<main class="sheet">
  <section class="values-panel">
    <div class="brand">
      <span class="brand-dot"></span>
      <span class="brand-name">BROLGA TRADE</span>
    </div>

    <svg class="values-diagram" viewBox="0 0 900 1200" aria-hidden="true">
      <path d="M280 345 Q330 352 360 407" fill="none" stroke="var(--green)" stroke-width="9"/>
      <path d="M360 410 C374 448 362 486 343 522" fill="none" stroke="var(--yellow)" stroke-width="9"/>
      <path d="M340 540 C322 556 300 550 278 557" fill="none" stroke="var(--charcoal)" stroke-width="9"/>

      <g fill="#ffffff" stroke-width="9">
        <circle cx="256" cy="278" r="63" stroke="var(--navy)"/>
        <circle cx="403" cy="363" r="63" stroke="var(--green)"/>
        <circle cx="403" cy="531" r="63" stroke="var(--yellow)"/>
        <circle cx="256" cy="616" r="63" stroke="var(--charcoal)"/>
      </g>
      <g fill="#ffffff" stroke="var(--ring-inner)" stroke-width="3">
        <circle cx="256" cy="278" r="54"/>
        <circle cx="403" cy="363" r="54"/>
        <circle cx="403" cy="531" r="54"/>
        <circle cx="256" cy="616" r="54"/>
      </g>
    </svg>

    <h1 class="values-title">OUR CORE<br>VALUES</h1>

    <article class="value value--excellence">
      <h2 class="value-name">Commitment to Excellence</h2>
      <p class="value-text">We turn up every day ready to be the best person we can be<br>and deliver the best possible outcome and experience for our<br>customer. Set a high bar and always seek to improve.</p>
    </article>

    <article class="value value--accuracy">
      <h2 class="value-name">Accuracy</h2>
      <p class="value-text">How we do the little things is how<br>we do everything. Detail matters.<br>We never assume…we make certain</p>
    </article>

    <article class="value value--growth">
      <h2 class="value-name">Growth</h2>
      <p class="value-text">Our knowledge, Experience, and<br>Skills. Personal &amp; professional. Be<br>curious and interested.</p>
    </article>

    <article class="value value--respect">
      <h2 class="value-name">Respect</h2>
      <p class="value-text">Listen first and understand.<br>Everyone is valued.</p>
    </article>
  </section>
</main>
</body>
</html>
```